Velorum Kinetics Business Card Contest

Velorum Kinetics is a b-b blockchain technology solutions company. We are seeking a professional yet minimalist business card to be designed. We would like the business card:1) to have a QR code to our website (velorum-k.example) somewhere on the card2) Colour/design to be somewhat relevant to our website (refer to attached image)3) Elegant-looking 4) No irrelevant iconsYou should use these information:Name: Eric BarbierDesignation: CEOPhone: +65 9752 2604Email: eric@triple-a.ioAddress: Singapore | China

```html
<!DOCTYPE html>
<html lang="en">
<head>
<meta charset="utf-8">
<title>Velorum Kinetics Business Card</title>
<link href="https://fonts.googleapis.com/css2?family=Work+Sans:wght@400;500&display=swap" rel="stylesheet">
<style>
  :root {
    --stage: #1c1c1e;
    --card-deep: #083f5c;
    --card-light: #155373;
    --ink: #dfe6ea;
    --ink-soft: #b9c7cf;
    --rule: #a9bac3;
  }
  * { box-sizing: border-box; margin: 0; padding: 0; }
  html, body {
    width: 1200px; height: 900px; overflow: hidden;
    background: var(--stage);
    font-family: "Work Sans", sans-serif;
  }
  .stage {
    position: relative; width: 1200px; height: 900px;
    display: flex; flex-direction: column; align-items: center; justify-content: center;
    gap: 44px;
  }
  .card {
    position: relative; width: 630px; height: 360px;
    background: linear-gradient(160deg, var(--card-light) 0%, var(--card-deep) 70%);
    color: var(--ink);
  }
  .card--front { display: flex; align-items: center; justify-content: center; }
  .brand {
    display: flex; align-items: center; gap: 14px;
    font-weight: 400; letter-spacing: 0.12em; text-transform: uppercase;
    color: var(--ink);
  }
  .brand__dot {
    width: 14px; height: 14px; border-radius: 50%;
    border: 2px solid var(--ink); flex: none;
  }
  .card--front .brand { font-size: 34px; }
  .card--back { display: flex; align-items: center; padding: 0 0 0 44px; }
  .card--back .brand { font-size: 22px; width: 270px; gap: 10px; }
  .card--back .brand__dot { width: 11px; height: 11px; }
  .divider { width: 1px; height: 170px; background: var(--rule); margin: 0 30px 0 12px; }
  .contact { display: flex; flex-direction: column; }
  .contact__name { font-size: 22px; font-weight: 500; letter-spacing: 0.03em; text-transform: uppercase; }
  .contact__role { font-size: 15px; color: var(--ink-soft); margin-top: 4px; }
  .contact__region { font-size: 16px; margin-top: 16px; letter-spacing: 0.02em; }
  .contact__list { list-style: none; margin-top: 10px; }
  .contact__item { display: flex; align-items: center; gap: 12px; font-size: 16px; line-height: 26px; letter-spacing: 0.02em; }
  .contact__icon { width: 12px; height: 12px; flex: none; }
</style>
</head>
<body>
<main class="stage">
  <section class="card card--front" aria-label="Card front">
    <div class="brand"><span>Velorum Kinetics</span><span class="brand__dot"></span></div>
  </section>

  <section class="card card--back" aria-label="Card back">
    <div class="brand"><span>Velorum Kinetics</span><span class="brand__dot"></span></div>
    <div class="divider"></div>
    <div class="contact">
      <p class="contact__name">Daniel Osgood</p>
      <p class="contact__role">CEO</p>
      <p class="contact__region">Singapore | China</p>
      <ul class="contact__list">
        <li class="contact__item">
          <svg class="contact__icon" viewBox="0 0 12 12" aria-hidden="true"><path d="M2.5 1h2l1 2.6-1.3 1a6 6 0 0 0 2.9 2.9l1-1.3 2.4 1v2.1c0 .5-.4.8-.9.8C5.2 10 1.8 6.6 1.7 1.9c0-.5.3-.9.8-.9z" fill="#dfe6ea"/></svg>
          <span>+65 8316 4079</span>
        </li>
        <li class="contact__item">
          <svg class="contact__icon" viewBox="0 0 12 12" aria-hidden="true"><rect x="1" y="2.5" width="10" height="7" fill="none" stroke="#dfe6ea" stroke-width="1.2"/><path d="M1 2.8 6 6.6l5-3.8" fill="none" stroke="#dfe6ea" stroke-width="1.2"/></svg>
          <span>daniel@velorum-k.example</span>
        </li>
        <li class="contact__item">
          <svg class="contact__icon" viewBox="0 0 12 12" aria-hidden="true"><circle cx="6" cy="6" r="5" fill="none" stroke="#dfe6ea" stroke-width="1.1"/><ellipse cx="6" cy="6" rx="2.2" ry="5" fill="none" stroke="#dfe6ea" stroke-width="1"/><path d="M1 6h10" stroke="#dfe6ea" stroke-width="1"/></svg>
          <span>www.velorum-k.example</span>
        </li>
      </ul>
    </div>
  </section>
</main>
</body>
</html>
```